Company or website name
- Quiet Hollow Properties
- Describe your company and organization and target audience
- We sell rural vacant, mostly residential land. Our target market is looking for privacy and either a place to retire to or a place to escape to.
- The design should have the following
- Mountains, Pine Trees, Earthy Colors, and match the attached logo. The home page should have designs for slides of properties at the top, followed by a survey (for users to share details of the property they're looking for), followed by search functionality, individual properties and general areas properties are available in. We'll also need at least one contact form on each page as well as maps. For the property detail page we'll need a large area for pictures, highlighted property details, a description and more detailed facts about property. The property detail page should also have a survey for users to share details of what they're looking for and contact form. Last but not least, similar properties should also be included on the property listing page. The winning design will include an excellent "Contact Us" page! Every page should have an opt-in offering users to be notified when new properties become available.
- Briefly describe your contest

```html
<!DOCTYPE html>
<html lang="en">
<head>
<meta charset="utf-8">
<title>Quiet Hollow Properties</title>
<link href="https://fonts.googleapis.com/css2?family=Noto+Serif:wght@400&family=Open+Sans:wght@400;600&family=Montserrat:wght@500;600;700&display=swap" rel="stylesheet">
<style>
:root{
  --teal:#1a5c52;
  --teal-dark:#134a41;
  --teal-field:#0f4238;
  --mint:#a8d1cd;
  --light:#f2f2f2;
  --white:#ffffff;
  --text:#333333;
  --muted:#666666;
}
*{box-sizing:border-box;margin:0;padding:0}
html,body{width:1200px;height:3139px;overflow:hidden}
body{position:relative;font-family:"Open Sans",sans-serif;color:var(--text);background:var(--white)}
.abs{position:absolute}
.band{position:absolute;left:0;width:1200px}
.topbar{top:0;height:37px;background:var(--teal);color:#fff;font-size:10px}
.topbar .item{position:absolute;top:12px;display:flex;align-items:center;gap:6px}
.nav{top:37px;height:63px;background:#fff}
.brand{position:absolute;left:35px;top:17px;display:flex;align-items:center;gap:6px;font-family:"Montserrat",sans-serif;font-weight:700;font-size:11px;color:var(--teal);letter-spacing:.5px}
.brand i{width:14px;height:14px;border-radius:50%;background:var(--teal);display:block}
.menu{position:absolute;top:26px;font-family:"Montserrat",sans-serif;font-size:11px;letter-spacing:1.3px;color:#444}
.menu.active{color:var(--teal)}
.hero{top:100px;height:574px;background:linear-gradient(180deg,#6f736f 0%,#55605a 35%,#3c4a44 60%,#3f5a55 78%,#4a3a2c 100%)}
.hero-title{top:182px;width:1200px;text-align:center;font-family:"Noto Serif",serif;font-size:28px;letter-spacing:7px;color:#fff}
.hero-sub{top:224px;width:1200px;text-align:center;font-size:12px;color:#fff}
.field{background:#fff;border-radius:3px;height:42px;color:#888;font-size:14px;display:flex;align-items:center;padding:0 10px;justify-content:space-between}
.chev{width:16px;height:10px}
.dots{top:540px;left:560px;display:flex;gap:22px;align-items:center}
.section-title{width:1200px;text-align:center;font-family:"Noto Serif",serif;color:var(--teal);font-size:29px;letter-spacing:6px}
.featured{top:674px;height:575px;background:var(--light)}
.card{position:absolute;background:#fff;box-shadow:0 1px 3px rgba(0,0,0,.18)}
.card .photo{width:100%;display:block}
.prop-card{top:112px;width:231px;height:329px;text-align:center}
.prop-card .photo{height:155px}
.prop-name{margin-top:18px;font-size:11px;line-height:17px;color:#333}
.prop-addr{margin-top:12px;font-size:13px;line-height:22px;color:#333}
.btn-solid{display:inline-block;margin-top:14px;width:125px;height:30px;line-height:30px;border-radius:15px;background:var(--teal);color:#fff;font-family:"Montserrat",sans-serif;font-weight:700;font-size:11px;letter-spacing:2px}
.btn-outline{position:absolute;border:2px solid var(--teal);color:var(--teal);font-size:13px;text-align:center;display:flex;align-items:center;justify-content:center;background:transparent}
.communities{top:1249px;height:405px;background:#fff}
.comm{position:absolute;top:99px;height:187px}
.comm-label{position:absolute;left:0;bottom:0;width:100%;height:53px;background:rgba(40,40,40,.75);color:#fff;font-size:13px;display:flex;align-items:center;justify-content:center}
.fade{opacity:.45}
.newsletter{top:1654px;height:151px;background:linear-gradient(90deg,#3e4f6e,#6a7487 30%,#8b8f9e 55%,#4b5a74 80%,#6f7a8e)}
.nl-title{left:235px;top:41px;font-family:"Montserrat",sans-serif;font-weight:600;font-size:18px;letter-spacing:1.6px;color:#fff}
.nl-text{left:235px;top:78px;width:330px;font-size:12px;line-height:18px;color:#f0f0f0}
.nl-input{left:610px;top:29px;width:355px;height:39px;background:#fff;font-size:15px;color:#555;padding-left:12px;display:flex;align-items:center;letter-spacing:1px}
.nl-btn{left:610px;top:83px;width:355px;height:39px;border:1.5px solid #fff;color:#fff;font-size:15px;letter-spacing:1.5px;display:flex;align-items:center;justify-content:center}
.testimonials{top:1805px;height:425px;background:#fff}
.tcard{position:absolute;top:97px;height:211px;background:var(--mint);padding:22px 19px;font-size:10px;color:#5d8c88}
.tcard.main{background:#fff;box-shadow:0 1px 4px rgba(0,0,0,.2);color:#333}
.qmark{width:24px;height:22px;background:var(--mint);color:#fff;font-family:"Noto Serif",serif;font-size:16px;text-align:center;line-height:24px}
.tcard.main .qmark{background:#8fc2bd}
.tcard .quote{margin-top:22px;line-height:22px;font-size:10.5px}
.tname{margin-top:18px;font-family:"Montserrat",sans-serif;font-size:11px;letter-spacing:1.2px}
.trole{margin-top:6px;font-size:8px}
.blog{top:2230px;height:585px;background:var(--light)}
.blog-card{top:115px;width:231px;height:341px}
.blog-card .photo{height:174px}
.blog-body{padding:10px 7px}
.blog-date{font-size:8.5px;color:#777}
.blog-head{margin-top:9px;font-size:11.5px;font-weight:600;line-height:18px;color:#333;text-align:justify;letter-spacing:.3px}
.blog-text{margin-top:10px;font-size:9px;line-height:18.5px;color:#777;text-align:justify}
.footer{top:2815px;height:286px;background:var(--teal);color:#fff}
.foot-head{font-family:"Montserrat",sans-serif;font-size:9px;letter-spacing:1.4px;font-weight:600}
.foot-small{font-size:9px;line-height:17.5px}
.ffield{position:absolute;left:734px;width:232px;background:var(--teal-field);border-bottom:1px solid #5d8c86;font-size:7.5px;padding:10px 7px;color:#e6e6e6}
.copybar{top:3101px;height:38px;background:var(--teal-dark);color:#fff;font-size:9px;display:flex;align-items:center;justify-content:center}
</style>
</head>
<body>

<header class="band topbar">
  <div class="item" style="left:36px">
    <svg width="12" height="12" viewBox="0 0 12 12"><circle cx="6" cy="6" r="6" fill="#4a8fd6"/><rect x="3" y="4" width="6" height="4" fill="none" stroke="#fff" stroke-width=".9"/><path d="M3 4l3 2.2L9 4" fill="none" stroke="#fff" stroke-width=".9"/></svg>
    info@quiethollowproperties.com
  </div>
  <div class="item" style="left:213px">
    <svg width="13" height="13" viewBox="0 0 12 12"><path d="M2 2l2.5-.5 1.2 2.5-1.4 1a6 6 0 0 0 3 3l1-1.4 2.5 1.2L10.3 10C6 10 2 6 2 2z" fill="#e8b64a"/></svg>
    +1 555 014 7788
  </div>
  <div class="item" style="left:1086px">
    <svg width="12" height="12" viewBox="0 0 12 12"><circle cx="6" cy="6" r="6" fill="#f1c232"/><circle cx="6" cy="5" r="2" fill="#fff"/><path d="M2.8 10a3.5 3.5 0 0 1 6.4 0" fill="#fff"/></svg>
    Login&nbsp; / &nbsp;Signup
  </div>
</header>

<nav class="band nav">
  <div class="brand"><i></i>QUIET HOLLOW</div>
  <span class="menu active" style="left:672px">HOME</span>
  <span class="menu" style="left:752px">PROPERTIES</span>
  <span class="menu" style="left:870px">ABOUT US</span>
  <span class="menu" style="left:976px">CONTACT</span>
  <span class="menu" style="left:1075px">BLOG</span>
  <svg class="abs" style="left:1143px;top:23px" width="18" height="18" viewBox="0 0 18 18"><circle cx="7.5" cy="7.5" r="6" fill="none" stroke="#333" stroke-width="1.6"/><path d="M12 12l5 5" stroke="#333" stroke-width="1.6"/></svg>
</nav>

<section class="band hero" role="img" aria-label="Mountain lake with pine forest and a wooden boathouse">
  <svg class="abs" style="left:34px;top:254px" width="14" height="24" viewBox="0 0 14 24"><path d="M12 2L2 12l10 10" fill="none" stroke="#fff" stroke-width="1.5"/></svg>
  <svg class="abs" style="left:1143px;top:251px" width="14" height="24" viewBox="0 0 14 24"><path d="M2 2l10 10-10 10" fill="none" stroke="#fff" stroke-width="1.5"/></svg>
  <h1 class="abs hero-title">WHAT ARE YOU LOOKING FOR?</h1>
  <p class="abs hero-sub">No matter what your property needs, Quiet Hollow Properties is here for you</p>
  <div class="abs field" style="left:336px;top:273px;width:124px">Buy / Sell<svg class="chev" viewBox="0 0 16 10"><path d="M1 1l7 7 7-7" fill="none" stroke="#777" stroke-width="1.5"/></svg></div>
  <div class="abs field" style="left:475px;top:273px;width:188px">Type of property<svg class="chev" viewBox="0 0 16 10"><path d="M1 1l7 7 7-7" fill="none" stroke="#777" stroke-width="1.5"/></svg></div>
  <div class="abs field" style="left:678px;top:273px;width:188px;padding:0">
    <span style="padding-left:11px;width:94px;border-right:1px solid #ddd;line-height:42px">$ Min</span>
    <span style="padding-left:11px;flex:1">$ Max</span>
  </div>
  <div class="abs field" style="left:336px;top:329px;width:530px;height:49px">Enter an address, neigborhood, city or ZIP code
    <svg width="28" height="28" viewBox="0 0 28 28"><circle cx="12" cy="12" r="10" fill="none" stroke="var(--teal)" stroke-width="2.2"/><path d="M19.5 19.5l7 7" stroke="var(--teal)" stroke-width="2.2"/></svg>
  </div>
  <div class="abs dots">
    <svg width="5" height="5"><circle cx="2.5" cy="2.5" r="2" fill="#fff"/></svg>
    <svg width="12" height="12" viewBox="0 0 12 12"><path d="M6 1l5 5-5 5-5-5z" fill="none" stroke="#fff"/><circle cx="6" cy="6" r="1.5" fill="#fff"/></svg>
    <svg width="12" height="12" viewBox="0 0 12 12"><path d="M6 1l5 5-5 5-5-5z" fill="none" stroke="#fff"/><circle cx="6" cy="6" r="1.5" fill="#fff"/></svg>
  </div>
</section>

<section class="band featured">
  <h2 class="abs section-title" style="top:40px">FEATURED PROPERTIES</h2>
  <article class="card prop-card" style="left:235px">
    <div class="photo" role="img" aria-label="White farmhouse with a wraparound porch on a green lawn" style="background:linear-gradient(180deg,#a9c8e6 0%,#dfe5ea 45%,#6e9a48 80%)"></div>
    <p class="prop-name">Redwood Forest Estate<br>Detail infomation</p>
    <p class="prop-addr">REDWOOD,<br>BLUE RAY WAY</p>
    <span class="btn-solid">READ MORE</span>
  </article>
  <article class="card prop-card" style="left:483px">
    <div class="photo" role="img" aria-label="Cottage with stone chimney and red door among trees" style="background:linear-gradient(180deg,#5f8f3e 0%,#8aa37a 50%,#3f6b2c 100%)"></div>
    <p class="prop-name">Redwood Forest Estate<br>Detail infomation</p>
    <p class="prop-addr">REDWOOD,<br>BLUE RAY WAY</p>
    <span class="btn-solid">READ MORE</span>
  </article>
  <article class="card prop-card" style="left:732px">
    <div class="photo" role="img" aria-label="Brick family home with a tidy front lawn" style="background:linear-gradient(180deg,#7ea9d9 0%,#b4c6d6 40%,#8a5a46 65%,#4f7a36 100%)"></div>
    <p class="prop-name">Redwood Forest Estate<br>Detail infomation</p>
    <p class="prop-addr">REDWOOD,<br>BLUE RAY WAY</p>
    <span class="btn-solid">READ MORE</span>
  </article>
  <div class="btn-outline" style="left:515px;top:492px;width:168px;height:37px">View our properties</div>
</section>

<section class="band communities">
  <h2 class="abs section-title" style="top:40px">AVAILABLE&nbsp; COMMUNITIES</h2>
  <div class="comm fade" style="left:0;width:216px;background:linear-gradient(180deg,#e7d9c6,#b9aa93)" role="img" aria-label="Sunlit suburban street lined with trees"></div>
  <div class="comm" style="left:234px;width:231px;background:linear-gradient(180deg,#cfdbe6 0%,#e3d8c4 40%,#b6a88e 80%,#7d8f5c 100%)" role="img" aria-label="Multi-storey beige townhouses with balconies"></div>
  <div class="comm" style="left:484px;width:231px;background:linear-gradient(180deg,#b9cfe0 0%,#a5453c 40%,#7ba04f 75%,#b7b7b0 100%)" role="img" aria-label="Red two-storey house with white porch and lawn">
    <div class="comm-label">Cedar Bend, NC</div>
  </div>
  <div class="comm" style="left:733px;width:232px;background:linear-gradient(180deg,#6b4a3a 0%,#8a6a58 40%,#3f6a38 75%,#2f4a2a 100%)" role="img" aria-label="Row of brownstone houses with leafy front gardens"></div>
  <div class="comm fade" style="left:984px;width:216px;background:linear-gradient(180deg,#c8d6e4,#d7cdb9 60%,#9fb0ae)" role="img" aria-label="Waterside villas under a pale sky"></div>
  <svg class="abs" style="left:34px;top:184px" width="12" height="20" viewBox="0 0 12 20"><path d="M10 1L2 10l8 9" fill="none" stroke="#444" stroke-width="1.4"/></svg>
  <svg class="abs" style="left:1143px;top:181px" width="12" height="20" viewBox="0 0 12 20"><path d="M2 1l8 9-8 9" fill="none" stroke="#444" stroke-width="1.4"/></svg>
  <div class="btn-outline" style="left:491px;top:321px;width:219px;height:37px">View available Communities</div>
</section>

<section class="band newsletter" role="img" aria-label="Blurred city lights background">
  <h3 class="abs nl-title">GET QUIET HOLLOW UPDATES:</h3>
  <p class="abs nl-text">For exclusive news and market updates sign up for our newsletter.</p>
  <div class="abs nl-input">Email</div>
  <div class="abs nl-btn">Get updates</div>
</section>

<section class="band testimonials">
  <h2 class="abs section-title" style="top:37px">TESTIMONIALS</h2>
  <div class="tcard" style="left:0;width:219px;padding-left:0;overflow:hidden">
    <p class="quote" style="margin-top:44px;margin-left:-60px;width:280px">Lorem ipsum dolor sit amet, consectetur adipiscing elit, sed do eiusmod tempor incididunt ut labore et dolore magna aliqua. Ut</p>
  </div>
  <div class="tcard main" style="left:237px;width:357px">
    <div class="qmark">&ldquo;</div>
    <p class="quote">Lorem ipsum dolor sit amet, consectetur adipiscing elit, sed do eiusmod tempor incididunt ut labore et dolore magna aliqua. Ut enim ad minim veniam.</p>
    <p class="tname">MARA ELLISON</p>
    <p class="trole">Happy Client</p>
  </div>
  <div class="tcard" style="left:613px;width:355px">
    <div class="qmark" style="background:#8fc2bd">&ldquo;</div>
    <p class="quote">Lorem ipsum dolor sit amet, consectetur adipiscing elit, sed do eiusmod tempor incididunt ut labore et dolore magna aliqua. Ut enim ad minim veniam.</p>
    <p class="tname">OWEN</p>
    <p class="trole">Happy Client</p>
  </div>
  <div class="tcard" style="left:988px;width:212px;overflow:hidden;white-space:nowrap">
    <div class="qmark" style="background:#8fc2bd">&ldquo;</div>
    <p class="quote">Lorem ipsum dolor sit amet, consectetur<br>eiusmod tempor incididunt ut labore et<br>enim ad minim veniam.</p>
    <p class="tname">OWEN</p>
    <p class="trole">Happy Client</p>
  </div>
  <svg class="abs" style="left:35px;top:2004px;top:199px" width="8" height="12" viewBox="0 0 8 12"><path d="M7 1L2 6l5 5" fill="none" stroke="#222" stroke-width="1.6"/></svg>
  <svg class="abs" style="left:1157px;top:199px" width="8" height="12" viewBox="0 0 8 12"><path d="M1 1l5 5-5 5" fill="none" stroke="#222" stroke-width="1.6"/></svg>
  <div class="btn-outline" style="left:475px;top:345px;width:251px;height:37px">Read more client testimonials</div>
</section>

<section class="band blog">
  <h2 class="abs section-title" style="top:42px">FROM OUR BLOG</h2>
  <article class="card blog-card" style="left:235px">
    <div class="photo" role="img" aria-label="Stone-front house with palm trees and lawn" style="background:linear-gradient(180deg,#8fb5dc 0%,#c9d3d6 40%,#7d7a70 65%,#6d9a44 100%)"></div>
    <div class="blog-body">
      <p class="blog-date">March 19, 2022</p>
      <p class="blog-head">Lorem ipsum dolor sit amet, consectetur adipiscing elit.</p>
      <p class="blog-text">Lorem ipsum dolor sit amet, consectetur adipiscing elit. Aliquam vel quam nibh. Nunc erat leo, viverra at purus ac, tincidunt tempor enim. Pellentesque in condimentum dui</p>
    </div>
  </article>
  <article class="card blog-card" style="left:485px">
    <div class="photo" role="img" aria-label="Mountain lake with a wooden boathouse" style="background:linear-gradient(180deg,#9aa0a0 0%,#6b756e 40%,#3f5b55 70%,#4a3c2e 100%)"></div>
    <div class="blog-body">
      <p class="blog-date">March 19, 2022</p>
      <p class="blog-head">Nunc erat leo, viverra at purus ac, tincidunt tempor enim.</p>
      <p class="blog-text">Lorem ipsum dolor sit amet, consectetur adipiscing elit. Aliquam vel quam nibh. Nunc erat leo, viverra at purus ac, tincidunt tempor enim. Pellentesque in condimentum dui</p>
    </div>
  </article>
  <article class="card blog-card" style="left:734px">
    <div class="photo" role="img" aria-label="Garden patio beside a pale blue house" style="background:linear-gradient(90deg,#3f6a38 0%,#5e8a4a 45%,#9fb8c6 70%,#c9d6de 100%)"></div>
    <div class="blog-body">
      <p class="blog-date">March 19, 2022</p>
      <p class="blog-head">viverra at purus ac, tincidunt tempor enim dui.</p>
      <p class="blog-text">Lorem ipsum dolor sit amet, consectetur adipiscing elit. Aliquam vel quam nibh. Nunc erat leo, viverra at purus ac, tincidunt tempor enim. Pellentesque in condimentum dui</p>
    </div>
  </article>
  <div class="btn-outline" style="left:515px;top:502px;width:168px;height:37px">Visit our blog</div>
</section>

<footer class="band footer">
  <div class="brand" style="left:235px;top:52px;color:#fff"><i style="background:#fff"></i>QUIET HOLLOW</div>
  <p class="abs foot-head" style="left:235px;top:104px">CONTACT US</p>
  <p class="abs foot-small" style="left:235px;top:120px">Phone number: +1 555 014 7788<br>Email: info@quiethollowproperties.com<br>Address: 214 Cedar Ridge Lane, Pine Falls</p>
  <p class="abs foot-head" style="left:482px;top:35px">SEARCH PROPERTY</p>
  <p class="abs foot-small" style="left:482px;top:66px;line-height:22.5px">Home for sale in Indiana<br>Home for sale in Maine<br>Home for sale in Massachusetts<br>Home for sale in Montana<br>Home for sale in South Carolina</p>
  <p class="abs foot-head" style="left:734px;top:35px">WE WOULD LOVE TO HEAR FROM YOU</p>
  <div class="ffield" style="top:58px;height:32px">Name</div>
  <div class="ffield" style="top:91px;height:42px;padding-top:14px">Email</div>
  <div class="ffield" style="top:134px;height:68px;padding-top:18px">Message</div>
  <div class="abs" style="left:734px;top:216px;width:100px;height:31px;border:1.5px solid #fff;font-family:Montserrat,sans-serif;font-size:9px;letter-spacing:1.6px;display:flex;align-items:center;justify-content:center">SEND</div>
</footer>
<div class="band copybar">Copyright © 2022 QuietHollowProperties- All Rights Reserved</div>

</body>
</html>
```